Exceptional Properties Flyer

I need a flyer template that I can re-use for high-end home listings over $1m in price. 11 X 17 horizontal folded to open wtih front photo shot large on front with short descriptionon areas, room for my photo, logo, contact info & property address then photo slots inside all pagers with room for copy to be plugged in. 3-4 photo spots per page at various sizes but room for bullet point descriptions on pages somewhere. Back of flyer larger photo slot and 2-3 smaller spots below with room for my photo and contact info
My contact info:
Maribel Oswick
Real Estate Broker
Halvorn Group Real Estate
Direct 206.555.0187
Email: maribel.oswic@tallowpine.com

```html
<!DOCTYPE html>
<html lang="en">
<head>
<meta charset="utf-8">
<title>Exceptional Properties Flyer</title>
<link rel="stylesheet" href="https://fonts.googleapis.com/css2?family=Caveat+Brush&family=Cormorant+Garamond:wght@500&family=Montserrat:wght@400;600;700&family=Roboto+Condensed:ital,wght@1,400;1,700;1,900&display=swap">
<style>
:root{
  --ink:#231f20;
  --paper:#ecedee;
  --white:#ffffff;
  --red:#d4202c;
  --slot:#8a898a;
  --muted:#6d6e70;
  --sheet:#ffffff;
}
*{box-sizing:border-box;margin:0;padding:0}
html,body{width:894px;height:1200px;overflow:hidden;background:var(--sheet)}
.stage{position:absolute;left:0;top:0;width:1110px;height:1490px;transform:scale(.80541);transform-origin:0 0}
.spread{position:absolute;left:35px;width:1040px;height:673px;background:var(--paper);overflow:hidden}
.spread--template{top:40px}
.spread--listing{top:767px}
.abs{position:absolute}
.ribbon{left:0;top:0}
.sale-tab{left:150px;top:0;width:172px;height:40px;background:var(--ink);color:var(--white);
  clip-path:polygon(0 0,100% 0,100% 62%,91% 100%,0 100%);
  font:500 25px/40px "Cormorant Garamond",serif;letter-spacing:1px;padding-left:28px}
.title-band{left:156px;top:40px;width:365px;height:75px;display:flex;align-items:center;justify-content:center}
.title{font:500 31px/1 "Cormorant Garamond",serif;color:var(--ink)}
.script{font-family:"Caveat Brush",cursive}
.script--red{color:var(--red)}
.script--white{color:var(--white)}
.price{left:5px;top:92px;width:145px;text-align:center}
.price-value{font:500 28px/1 "Cormorant Garamond",serif;color:#3a3536}
.price-label{font:400 10px/1 Montserrat,sans-serif;color:var(--muted);margin-top:6px}
.features{left:0;top:180px;width:156px;list-style:none;text-align:center;color:var(--white);
  font:400 10.5px/19px "Roboto Condensed",sans-serif;font-style:italic;text-transform:uppercase}
.features b{font-weight:900}
.features-note{left:0;top:238px;width:156px;text-align:center;font-size:27px;line-height:24px}
.slot{background:var(--slot)}
.photo-main{left:156px;top:115px;width:365px;height:230px}
.photo-small{top:347px;height:99px}
.photo-small--a{left:156px;width:118px}
.photo-small--b{left:278px;width:120px}
.photo-small--c{left:401px;width:120px}
.photo-wide{left:521px;width:519px}
.photo-wide--top{top:0;height:320px}
.photo-wide--bottom{top:370px;height:303px}
.feature-band{left:521px;top:320px;width:519px;height:50px;background:var(--ink);display:flex;align-items:center;justify-content:center;color:var(--white)}
.feature-title{font:500 40px/1 "Cormorant Garamond",serif;letter-spacing:.5px}
.slot-note{display:flex;align-items:center;justify-content:center;font-size:48px}
.brand{left:12px;top:462px;width:140px;color:var(--ink);font-family:Montserrat,sans-serif;text-align:center}
.brand-name{font-weight:700;font-size:25px;letter-spacing:-.5px;display:flex;align-items:center;justify-content:center;gap:6px}
.brand-mark{width:10px;height:10px;background:var(--ink)}
.brand-tag{font-weight:400;font-size:12.5px;letter-spacing:1.6px;margin-top:22px;font-variant:small-caps}
.address{left:168px;top:458px;font:700 13px/1 "Roboto Condensed",sans-serif;font-style:italic;text-transform:uppercase;color:var(--ink);letter-spacing:.3px}
.description{left:190px;top:484px;width:320px;font:400 8.4px/11px "Roboto Condensed",sans-serif;font-style:italic;text-transform:uppercase;color:var(--ink)}
.closing{left:190px;top:532px;font:700 10px/1 "Roboto Condensed",sans-serif;font-style:italic;text-transform:uppercase;color:var(--ink)}
.note-address{left:168px;top:455px;font-size:18px}
.note-description{left:246px;top:508px;font-size:24px}
.agent{left:6px;top:571px;width:515px;height:84px;background:var(--ink);color:var(--white);font-family:Montserrat,sans-serif}
.agent-photo{left:6px;top:5px;width:75px;height:75px;background:linear-gradient(160deg,#d9c7a4 0%,#b89a6e 45%,#2a2324 100%)}
.agent-offered{left:91px;top:12px;font-size:8.5px;color:#d7d7d7}
.agent-name{left:91px;top:24px;font-size:17px;font-weight:700;white-space:nowrap}
.agent-name span{font-size:11.5px;font-weight:600;color:#d7d7d7}
.agent-company{left:91px;top:51px;font-size:8px;color:#bdbdbd;text-transform:uppercase}
.agent-line{left:91px;top:63px;font-size:8.5px;color:#cfcfcf;white-space:nowrap}
.agent-line b{color:var(--white);font-size:11.5px;font-weight:700;margin:0 8px 0 3px}
.agent-line strong{color:var(--white);font-weight:700;margin-left:3px}
.img-house{background:linear-gradient(180deg,#14195a 0%,#2c3a82 30%,#e9e6df 55%,#8a5a34 80%,#5b3a22 100%)}
.img-lounge{background:linear-gradient(180deg,#efe6da 0%,#c9a98a 60%,#8b6a52 100%)}
.img-bath{background:linear-gradient(135deg,#bfc4c0 0%,#7ec23c 50%,#dfe3df 100%)}
.img-kitchen{background:linear-gradient(180deg,#f0ebe3 0%,#a77b52 55%,#5a3b24 100%)}
.img-exterior{background:linear-gradient(180deg,#10154f 0%,#273680 28%,#ecebe6 55%,#8b5d38 82%,#4f3320 100%)}
.img-pool{background:linear-gradient(180deg,#8fb7df 0%,#3f6b34 35%,#cfa986 65%,#46b9d6 85%,#2f97c0 100%)}
</style>
</head>
<body>
<div class="stage">

  <section class="spread spread--template" aria-label="Flyer layout guide">
    <svg class="abs ribbon" width="156" height="446" viewBox="0 0 156 446" aria-hidden="true">
      <rect width="156" height="446" fill="var(--ink)"/>
      <polygon points="5,0 150,0 150,173 78,150 5,173" fill="var(--paper)"/>
      <polygon points="0,446 78,400 156,446" fill="var(--paper)"/>
    </svg>
    <div class="abs sale-tab">FOR SALE</div>
    <div class="abs title-band"><span class="script script--red" style="font-size:40px">title</span></div>
    <div class="abs price"><div class="script script--red" style="font-size:32px;line-height:1">price</div><div class="price-label" style="margin-top:0">Property asking price</div></div>
    <div class="abs features-note script script--white">space for<br>features<br>listing</div>
    <div class="abs slot photo-main"></div>
    <div class="abs slot photo-small photo-small--a"></div>
    <div class="abs slot photo-small photo-small--b"></div>
    <div class="abs slot photo-small photo-small--c"></div>
    <div class="abs slot photo-wide photo-wide--top slot-note script script--white">extra picture</div>
    <div class="abs feature-band"><span class="script" style="font-size:50px">fancy title</span></div>
    <div class="abs slot photo-wide photo-wide--bottom slot-note script script--white">extra picture</div>
    <div class="abs brand"><div class="brand-name"><span class="brand-mark"></span>Tallowpine</div><div class="brand-tag">Real Estate Center</div></div>
    <div class="abs note-address script script--red">Property address</div>
    <div class="abs note-description script script--red">space for description</div>
    <div class="abs agent">
      <div class="abs agent-photo" role="img" aria-label="Agent portrait photo"></div>
      <div class="abs agent-offered">Offered By</div>
      <div class="abs agent-name">Maribel Oswick, <span>Real Estate Broker</span></div>
      <div class="abs agent-company">Halvorn Group Real Estate</div>
      <div class="abs agent-line">Direct: <b>206.555.0187</b> Email: <strong>maribel.oswic@tallowpine.com</strong></div>
    </div>
  </section>

  <section class="spread spread--listing" aria-label="Finished listing flyer">
    <svg class="abs ribbon" width="156" height="446" viewBox="0 0 156 446" aria-hidden="true">
      <rect width="156" height="446" fill="var(--ink)"/>
      <polygon points="5,0 150,0 150,173 78,150 5,173" fill="var(--paper)"/>
      <polygon points="0,446 78,400 156,446" fill="var(--paper)"/>
    </svg>
    <div class="abs sale-tab">FOR SALE</div>
    <div class="abs title-band"><h1 class="title">Amazing Multi Level Home</h1></div>
    <div class="abs price"><div class="price-value">1,500 000</div><div class="price-label">Property asking price</div></div>
    <ul class="abs features">
      <li><b>Big family</b> house</li>
      <li><b>Year build :</b> 2013</li>
      <li><b>8</b> bedrooms</li>
      <li><b>3</b> baths</li>
      <li><b>Appeox.</b> 3000sq. ft.</li>
      <li><b>Air</b> heat</li>
      <li><b>Air</b> conditioning</li>
      <li><b>3</b> car garage</li>
      <li><b>City</b> views</li>
      <li><b>Fenced</b> backyard</li>
      <li><b>Swimming</b> pool</li>
    </ul>
    <div class="abs photo-main img-house" role="img" aria-label="Modern white multi-level house at dusk with timber deck and outdoor dining"></div>
    <div class="abs photo-small photo-small--a img-lounge" role="img" aria-label="Bright living room with sofa"></div>
    <div class="abs photo-small photo-small--b img-bath" role="img" aria-label="Bathroom with green feature wall"></div>
    <div class="abs photo-small photo-small--c img-kitchen" role="img" aria-label="Wood-finished kitchen"></div>
    <div class="abs photo-wide photo-wide--top img-exterior" role="img" aria-label="Rear view of the house at dusk with deck and palms"></div>
    <div class="abs feature-band"><h2 class="feature-title">Amazing Multi Level Home</h2></div>
    <div class="abs photo-wide photo-wide--bottom img-pool" role="img" aria-label="Garden terrace with shade sail and swimming pool"></div>
    <div class="abs brand"><div class="brand-name"><span class="brand-mark"></span>Tallowpine</div><div class="brand-tag">Real Estate Center</div></div>
    <div class="abs address">Property address, XYZ street 6743 NJ</div>
    <p class="abs description">Sunlit open rooms flow onto a wide timber deck and sheltered pool terrace. The kitchen, dining and family lounge share garden views, while the upper level offers a quiet primary suite with private balcony and soaking tub. Minutes from parks, shops and schools.</p>
    <div class="abs closing">Et lab ini dolut vel ipiduci te velest l ipiduci te velest</div>
    <div class="abs agent">
      <div class="abs agent-photo" role="img" aria-label="Agent portrait photo"></div>
      <div class="abs agent-offered">Offered By</div>
      <div class="abs agent-name">Maribel Oswick, <span>Real Estate Broker</span></div>
      <div class="abs agent-company">Halvorn Group Real Estate</div>
      <div class="abs agent-line">Direct: <b>206.555.0187</b> Email: <strong>maribel.oswic@tallowpine.com</strong></div>
    </div>
  </section>

</div>
</body>
</html>
```